Purple Heart Veteran Owned Telecommunications Company

I need to develop my current website (brightwirel.com) into something more upbeat and modern. I created the existing one with SiteKindle and it's very basic. I'm open to using any type of website builder and not just SiteKindle. I feel like SiteKindle is pretty basic. I want something customized to me and my company. I plan on doing a Zorbix Ad, Email Marketing, and Mail Marketing campaign and SEO push. I want a website built so they can look up my company. We are a low voltage telecommunications company based out of Chicago. We are a General Contractor and I have technicians all throughout the US and Canada. I mainly appeal to the government and fortune 500 companies across the country. I focus on commercial and federal work with minor work in Residential. I need to appeal to everyone and not just locally. My company name is Brightwirel. I'm a Marine Corps veteran and my I created the company with my son in mind. We are a service disabled veteran owned small business. I'm open to any play on my logo or color scheme. I do like the color blue but I'm open to anything again. I would like a website that has little maintenance needed and something that is modern and sticks out with my competitors. I'm only in business for 2 years but I need to stick out to my competition so I can start building revenue through ads and getting my name out there with limited funds. I did have a logo and name created which I'm attaching. I'm completely open to changing it if someone can come up with something creative. I would like someone that understands SEO and can help feed work to my site. I'm also open to paying more for the right website that gets everything I want. I know I need to add more pages and more professional. Please use my website as a template but also feel free to come up with any new ideas. I would like some feedback or ideas on what else to add to my website or remove so I can appeal to my audience and look more authentic.

Target Market(s)

Commercial Companies locally in Chicago, and Fortune 500 companies and the government

Industry/Entity Type

Telecommunications

Coding

Number of Pages Required

Font styles to use
Sans Serif

Requirements
Must have
• A Modern, fresh look that is customized and original. Something that sticks out to my customers.
Nice to have
• Anything that sticks out and isn't stock. I'm open to anything that is unique and different.
Should not have
• Nothing Generic. I would like something custom tailored to my business

```html
<!DOCTYPE html>
<html lang="en">
<head>
<meta charset="utf-8">
<title>Brightwirel General Contractor</title>
<link href="https://fonts.googleapis.com/css2?family=Lato:wght@400;700;900&display=swap" rel="stylesheet">
<style>
:root{
  --blue:#1f55d4;
  --blue-deep:#17318f;
  --orange:#f1561c;
  --ink:#1f1f22;
  --text:#4b4b4f;
  --muted:#7a7a7e;
  --grey-bg:#f2f2f3;
  --footer:#1d1d20;
  --footer-deep:#141416;
  --white:#ffffff;
}
*{margin:0;padding:0;box-sizing:border-box}
html,body{width:1200px;height:3474px;overflow:hidden}
body{position:relative;font-family:'Lato',sans-serif;color:var(--text);background:var(--white)}
.abs{position:absolute}
.btn{position:absolute;display:flex;align-items:center;padding-left:32px;width:215px;height:50px;background:var(--orange);color:var(--white);font-weight:900;font-size:19px;letter-spacing:.3px;clip-path:polygon(0 0,100% 0,calc(100% - 28px) 100%,0 100%)}

/* header */
.topbar{left:593px;top:0;width:607px;height:50px;background:var(--orange);clip-path:polygon(0 0,100% 0,100% 100%,42px 100%);color:var(--white);font-weight:700;font-size:22px;display:flex;align-items:center;gap:14px;padding-left:60px}
.topbar svg{flex:none}
.topbar .gap{width:22px}
.brand{left:74px;top:58px;display:flex;align-items:center;gap:12px;color:var(--blue);font-weight:900;font-size:30px;letter-spacing:1.5px}
.brand i{width:24px;height:24px;border-radius:50%;background:var(--orange);display:block}
.nav{left:503px;top:94px;display:flex;gap:0;font-weight:700;font-size:17px;color:var(--ink)}
.nav a{position:absolute;white-space:nowrap;text-decoration:none;color:inherit}
.nav a.active{color:var(--blue)}

/* hero */
.hero{left:0;top:151px;width:1200px;height:725px;clip-path:polygon(0 0,100% 0,100% 627px,50% 725px,0 627px);background:linear-gradient(115deg,#3a2bb8 0%,#6a2fc9 22%,#2549c9 48%,#1a64c8 70%,#173f9d 100%)}
.hero-glow{left:0;top:151px;width:1200px;height:725px;clip-path:polygon(0 0,100% 0,100% 627px,50% 725px,0 627px);background:radial-gradient(circle at 18% 20%,rgba(230,60,220,.45),transparent 40%),radial-gradient(circle at 70% 70%,rgba(80,220,140,.25),transparent 35%),radial-gradient(circle at 85% 40%,rgba(255,220,90,.25),transparent 30%)}
.hero-title{left:0;width:1200px;top:372px;text-align:center;color:var(--white);font-weight:900;font-size:104px;line-height:1;letter-spacing:1px}
.hero-sub{left:0;width:1200px;top:484px;text-align:center;color:var(--white);font-weight:900;font-size:54px;line-height:1}
.dots{left:562px;top:753px;display:flex;gap:9px}
.dots span{width:12px;height:12px;border-radius:50%;background:var(--orange)}
.dots span:first-child{background:var(--white)}

/* about */
.about-photo{left:74px;top:954px;width:472px;height:408px;background:linear-gradient(135deg,#1f4fc2 0%,#2a3a7a 35%,#c9561f 65%,#f06a20 100%)}
.eyebrow{font-weight:700;font-size:20px;color:var(--muted)}
.h2{font-weight:900;font-size:38px;color:var(--blue);line-height:1.15}
.para{font-size:17.5px;line-height:32px;color:var(--text)}

/* low voltage */
.lv{left:0;top:1437px;width:1200px;height:533px;background:linear-gradient(100deg,#1d4fd0 0%,#3752b8 35%,#b55a3c 60%,#f0551a 80%)}
.lv-photo{left:708px;top:1437px;width:492px;height:533px;clip-path:polygon(0 0,100% 0,100% 100%,102px 100%);background:linear-gradient(160deg,#3a4a66 0%,#8a93a8 40%,#2f3b57 75%,#1a2238 100%)}
.lv-fade{left:690px;top:1437px;width:160px;height:533px;background:linear-gradient(90deg,rgba(240,85,26,.85),rgba(240,85,26,0))}
.lv .white{color:var(--white)}
.services{left:406px;top:1534px;width:720px;height:338px;background:rgba(255,255,255,.95);padding:32px 0 0 28px}
.services h3{font-weight:900;font-size:30px;color:var(--blue);margin-bottom:12px}
.svc-list{position:absolute;list-style:none;font-size:15px;color:var(--ink)}
.svc-list li{height:36px;display:flex;align-items:center;gap:16px}

/* markets */
.center{left:0;width:1200px;text-align:center}
.card{position:absolute;top:2188px;width:241px;height:230px;border:1px solid #dcdcdc;background:var(--white);text-align:center}
.card .icon{position:absolute;left:78px;top:-40px;width:84px;height:84px;border-radius:50%;display:flex;align-items:center;justify-content:center}
.card h4{position:absolute;top:64px;width:100%;font-weight:900;font-size:26px;color:var(--ink)}
.card p{position:absolute;top:104px;left:24px;right:24px;font-size:14.5px;line-height:27px;color:var(--text)}
.o{background:var(--orange)} .b{background:var(--blue)}
.arrow{top:2288px}

/* team */
.team{left:0;top:2480px;width:1200px;height:591px;background:var(--grey-bg)}
.member-photo{position:absolute;top:2618px;width:330px;height:197px}
.member h4{position:absolute;top:2834px;font-weight:900;font-size:25px;color:var(--ink);white-space:nowrap}
.member p{position:absolute;top:2874px;font-size:14.5px;line-height:27px;color:var(--text);width:300px}

/* footer */
.footer{left:0;top:3071px;width:1200px;height:326px;background:var(--footer)}
.footer-bar{left:0;top:3397px;width:1200px;height:77px;background:var(--footer-deep)}
.f-brand{left:74px;top:3210px;display:flex;align-items:center;gap:10px;color:#c9c9cc;font-weight:400;font-size:28px;letter-spacing:1.5px}
.f-brand i{width:18px;height:18px;border-radius:50%;background:#c9c9cc;display:block}
.f-head{font-weight:900;font-size:18px;color:var(--orange)}
.f-links{list-style:none;font-size:15px;color:#dedee0}
.f-links li{height:33px}
.f-input{left:883px;top:3179px;width:243px;height:47px;background:var(--white);border:1px solid #ccc;font-size:13px;color:#333;padding:14px 10px}
.f-btn{left:883px;top:3237px;width:108px;height:46px;background:var(--blue);color:var(--white);font-weight:900;font-size:14px;display:flex;align-items:center;padding-left:18px;clip-path:polygon(0 0,100% 0,calc(100% - 16px) 100%,0 100%)}
.copy{left:75px;top:3426px;font-size:14px;color:#dedee0}
.social{left:842px;top:3424px;display:flex;gap:12px;font-size:13px;font-weight:700;color:#dedee0}
</style>
</head>
<body>

<!-- header -->
<div class="abs topbar">
  <svg width="20" height="20" viewBox="0 0 24 24" fill="#fff"><path d="M6.6 10.8a15.1 15.1 0 0 0 6.6 6.6l2.2-2.2c.3-.3.7-.4 1-.2 1.1.4 2.3.6 3.6.6.6 0 1 .4 1 1V20c0 .6-.4 1-1 1A17 17 0 0 1 3 4c0-.6.4-1 1-1h3.5c.6 0 1 .4 1 1 0 1.2.2 2.4.6 3.6.1.3 0 .7-.2 1z"/></svg>
  <span>312-555-0148</span><span class="gap"></span>
  <svg width="22" height="16" viewBox="0 0 22 16" fill="#fff"><path d="M0 0h22v2l-11 7L0 2z"/><path d="M0 4l11 7 11-7v12H0z"/></svg>
  <span>info@brightwirel.com</span>
</div>
<div class="abs brand"><i></i>BRIGHTWIREL</div>
<nav class="abs nav" style="left:0;top:94px">
  <a class="active" style="left:503px">HOME</a>
  <a style="left:600px">LOW VOLTAGE</a>
  <a style="left:763px">MARKETS</a>
  <a style="left:887px">OUR TEAM</a>
  <a style="left:1020px">CONTACT US</a>
</nav>

<!-- hero -->
<div class="abs hero" role="img" aria-label="Close-up photo of network switch with blue patch cables and fibre lines in violet light"></div>
<div class="abs hero-glow"></div>
<h1 class="abs hero-title">BRIGHTWIREL</h1>
<div class="abs hero-sub">GENERAL CONTRACTOR</div>
<a class="btn" style="left:495px;top:569px;width:215px">READ MORE</a>
<div class="abs dots"><span></span><span></span><span></span><span></span></div>

<!-- about -->
<div class="abs about-photo" role="img" aria-label="Photo of a technician working in a server room, tinted blue and orange"></div>
<div class="abs eyebrow" style="left:616px;top:950px">WHO WE ARE</div>
<h2 class="abs h2" style="left:616px;top:981px;width:560px">WELCOME TO BRIGHTWIREL GENERAL CONTRACTOR</h2>
<p class="abs para" style="left:616px;top:1082px;width:515px">Sed ut perspiciatis unde omnis iste natus error sit voluptatem accusantium doloremque laudantium, totam rem aperiam, eaque ipsa quae ab illo inventore veritatis et quasi architecto beatae vitae dicta sunt explicabo. Nemo enim ipsam voluptatem quia voluptas sit aspernatur aut odit aut fugit, sed quia consequuntur magni dolores eos qui ratione voluptatem sequi nesciunt.</p>
<a class="btn" style="left:616px;top:1313px">READ MORE</a>

<!-- low voltage -->
<section class="abs lv"></section>
<div class="abs lv-fade"></div>
<div class="abs lv-photo" role="img" aria-label="Photo of a technician connecting cables at a server rack"></div>
<div class="abs eyebrow" style="left:74px;top:1521px;color:#fff;font-weight:900">WHAT WE DO</div>
<h2 class="abs h2" style="left:74px;top:1552px;color:#fff">LOW VOLTAGE</h2>
<p class="abs para" style="left:74px;top:1609px;width:310px;color:#fff">Sed ut perspiciatis unde omnis iste natus error sit voluptatem accusantium doloremque laudantium, totam rem aperiam, eaque ipsa quae ab illo inventore veritatis et quasi architecto beatae sequi nesciunt.</p>
<a class="btn" style="left:74px;top:1830px">READ MORE</a>

<div class="abs services">
  <h3>SERVICES</h3>
  <ul class="svc-list" style="left:28px;top:74px">
    <li><svg width="15" height="15" viewBox="0 0 16 16"><circle cx="8" cy="8" r="7" fill="none" stroke="#1f55d4" stroke-width="1.6"/><path d="M4.8 8.2l2.2 2.2 4.2-4.4" fill="none" stroke="#1f55d4" stroke-width="1.8"/></svg>Low Voltage Wiring and Cabling</li>
    <li><svg width="15" height="15" viewBox="0 0 16 16"><circle cx="8" cy="8" r="7" fill="none" stroke="#1f55d4" stroke-width="1.6"/><path d="M4.8 8.2l2.2 2.2 4.2-4.4" fill="none" stroke="#1f55d4" stroke-width="1.8"/></svg>Voice and Data Network Cabling</li>
    <li><svg width="15" height="15" viewBox="0 0 16 16"><circle cx="8" cy="8" r="7" fill="none" stroke="#1f55d4" stroke-width="1.6"/><path d="M4.8 8.2l2.2 2.2 4.2-4.4" fill="none" stroke="#1f55d4" stroke-width="1.8"/></svg>CAT 3/5/6, Fiber Optic, and Coax Cabling</li>
    <li><svg width="15" height="15" viewBox="0 0 16 16"><circle cx="8" cy="8" r="7" fill="none" stroke="#1f55d4" stroke-width="1.6"/><path d="M4.8 8.2l2.2 2.2 4.2-4.4" fill="none" stroke="#1f55d4" stroke-width="1.8"/></svg>Single and Multiple Floor Installations</li>
    <li><svg width="15" height="15" viewBox="0 0 16 16"><circle cx="8" cy="8" r="7" fill="none" stroke="#1f55d4" stroke-width="1.6"/><path d="M4.8 8.2l2.2 2.2 4.2-4.4" fill="none" stroke="#1f55d4" stroke-width="1.8"/></svg>Server Racks/Networking Setup</li>
    <li><svg width="15" height="15" viewBox="0 0 16 16"><circle cx="8" cy="8" r="7" fill="none" stroke="#1f55d4" stroke-width="1.6"/><path d="M4.8 8.2l2.2 2.2 4.2-4.4" fill="none" stroke="#1f55d4" stroke-width="1.8"/></svg>Audio/Video Cabling and Wiring</li>
  </ul>
  <ul class="svc-list" style="left:392px;top:74px">
    <li><svg width="15" height="15" viewBox="0 0 16 16"><circle cx="8" cy="8" r="7" fill="none" stroke="#1f55d4" stroke-width="1.6"/><path d="M4.8 8.2l2.2 2.2 4.2-4.4" fill="none" stroke="#1f55d4" stroke-width="1.8"/></svg>WiFi - Wireless Network Installation</li>
    <li><svg width="15" height="15" viewBox="0 0 16 16"><circle cx="8" cy="8" r="7" fill="none" stroke="#1f55d4" stroke-width="1.6"/><path d="M4.8 8.2l2.2 2.2 4.2-4.4" fill="none" stroke="#1f55d4" stroke-width="1.8"/></svg>Access Point Installation</li>
    <li><svg width="15" height="15" viewBox="0 0 16 16"><circle cx="8" cy="8" r="7" fill="none" stroke="#1f55d4" stroke-width="1.6"/><path d="M4.8 8.2l2.2 2.2 4.2-4.4" fill="none" stroke="#1f55d4" stroke-width="1.8"/></svg>Voice &amp; Telephone Wiring</li>
    <li><svg width="15" height="15" viewBox="0 0 16 16"><circle cx="8" cy="8" r="7" fill="none" stroke="#1f55d4" stroke-width="1.6"/><path d="M4.8 8.2l2.2 2.2 4.2-4.4" fill="none" stroke="#1f55d4" stroke-width="1.8"/></svg>Demarc Extension</li>
    <li><svg width="15" height="15" viewBox="0 0 16 16"><circle cx="8" cy="8" r="7" fill="none" stroke="#1f55d4" stroke-width="1.6"/><path d="M4.8 8.2l2.2 2.2 4.2-4.4" fill="none" stroke="#1f55d4" stroke-width="1.8"/></svg>Security Camera Installation</li>
    <li><svg width="15" height="15" viewBox="0 0 16 16"><circle cx="8" cy="8" r="7" fill="none" stroke="#1f55d4" stroke-width="1.6"/><path d="M4.8 8.2l2.2 2.2 4.2-4.4" fill="none" stroke="#1f55d4" stroke-width="1.8"/></svg>Heat Mapping</li>
  </ul>
</div>

<!-- markets -->
<div class="abs eyebrow center" style="top:2027px">AREA WE SERVES</div>
<h2 class="abs h2 center" style="top:2058px">OUR MARKETS</h2>
<svg class="abs arrow" style="left:46px" width="16" height="28" viewBox="0 0 16 28"><path d="M14 2L3 14l11 12" fill="none" stroke="#555" stroke-width="2"/></svg>
<svg class="abs arrow" style="left:1138px" width="16" height="28" viewBox="0 0 16 28"><path d="M2 2l11 12L2 26" fill="none" stroke="#555" stroke-width="2"/></svg>

<div class="card" style="left:74px">
  <div class="icon o"><svg width="42" height="38" viewBox="0 0 42 38" fill="#fff"><path d="M21 2L2 19h5v17h10V26h8v10h10V19h5z"/></svg></div>
  <h4>Residential</h4><p>Let us assist you with your project! No project is to big or small.</p>
</div>
<div class="card" style="left:344px">
  <div class="icon b"><svg width="30" height="42" viewBox="0 0 30 42" fill="#fff"><path d="M2 2h26v38H18v-8h-6v8H2z"/><g fill="#1f55d4"><rect x="8" y="8" width="4" height="4"/><rect x="18" y="8" width="4" height="4"/><rect x="8" y="16" width="4" height="4"/><rect x="18" y="16" width="4" height="4"/><rect x="8" y="24" width="4" height="4"/><rect x="18" y="24" width="4" height="4"/></g></svg></div>
  <h4>Commercial</h4><p>Let us assist you with your project! No project is to big or small.</p>
</div>
<div class="card" style="left:613px">
  <div class="icon o"><svg width="46" height="44" viewBox="0 0 46 44" fill="#fff"><path d="M23 2v4M12 16a11 9 0 0 1 22 0z"/><rect x="21.5" y="1" width="3" height="8"/><rect x="6" y="17" width="34" height="4"/><rect x="9" y="23" width="4" height="13"/><rect x="17" y="23" width="4" height="13"/><rect x="25" y="23" width="4" height="13"/><rect x="33" y="23" width="4" height="13"/><rect x="3" y="37" width="40" height="5"/></svg></div>
  <h4>Federal</h4><p>Let us assist you with your project! No project is to big or small.</p>
</div>
<div class="card" style="left:883px">
  <div class="icon b"><svg width="40" height="36" viewBox="0 0 40 36" fill="#fff"><rect x="2" y="2" width="36" height="9" rx="2"/><rect x="2" y="14" width="36" height="9" rx="2"/><rect x="2" y="26" width="36" height="9" rx="2"/><g fill="#1f55d4"><circle cx="8" cy="6.5" r="1.6"/><circle cx="8" cy="18.5" r="1.6"/><circle cx="8" cy="30.5" r="1.6"/></g></svg></div>
  <h4>Data Centers</h4><p>Let us assist you with your project! No project is to big or small.</p>
</div>

<!-- team -->
<section class="abs team"></section>
<h2 class="abs h2 center" style="top:2543px">OUR TEAM</h2>

<div class="member">
  <div class="member-photo" style="left:74px;background:linear-gradient(135deg,#5a5446,#2f2c26 60%,#8a8680)" role="img" aria-label="Photo of a veteran in uniform on a phone call at a laptop"></div>
  <h4 style="left:74px">Veteran Owned (SDVOSB)</h4>
  <p style="left:74px;width:330px">Brightwirel, your partner for life. Brightwirel is 100% owned and operated.</p>
  <a class="btn" style="left:74px;top:2950px">READ MORE</a>
</div>
<div class="member">
  <div class="member-photo" style="left:435px;background:linear-gradient(135deg,#8e949c,#3b4654 55%,#c2c6cc)" role="img" aria-label="Photo of a young technician wiring an electrical panel"></div>
  <h4 style="left:435px">Hiring Veterans</h4>
  <p style="left:435px">More than 60% of our field technicians are veterans.</p>
  <a class="btn" style="left:435px;top:2950px">READ MORE</a>
</div>
<div class="member">
  <div class="member-photo" style="left:797px;background:linear-gradient(135deg,#6e8a52,#2c4f9e 55%,#a7b46a)" role="img" aria-label="Photo of smiling contractors in hi-vis vests holding cable coils outdoors"></div>
  <h4 style="left:794px">National Team of Contractors</h4>
  <p style="left:794px;width:320px">Brightwirel is based out of Chicago but has a national team of experienced</p>
  <a class="btn" style="left:794px;top:2950px">READ MORE</a>
</div>

<!-- footer -->
<footer class="abs footer"></footer>
<div class="abs footer-bar"></div>
<div class="abs f-brand"><i></i>BRIGHTWIREL</div>

<div class="abs f-head" style="left:341px;top:3131px">QUICK LINKS</div>
<ul class="abs f-links" style="left:341px;top:3170px"><li>Home</li><li>Low Voltage</li><li>Markets</li><li>Our Team</li><li>Contact Us</li></ul>

<div class="abs f-head" style="left:563px;top:3131px">MARKETS</div>
<ul class="abs f-links" style="left:563px;top:3170px"><li>Residential</li><li>Commercial</li><li>Federal</li><li>Retail</li><li>Data Centers</li></ul>
<ul class="abs f-links" style="left:705px;top:3170px"><li>Mixed-Use</li><li>Hospitality</li><li>Education</li><li>Senior Living</li></ul>

<div class="abs f-head" style="left:883px;top:3131px">EMAIL SIGN UP</div>
<div class="abs f-input">Email Address</div>
<div class="abs f-btn">SIGN UP</div>

<div class="abs copy">Copyright © 2021 Brightwirel All Rights Reserved.</div>
<div class="abs social"><span>Linkly</span><span>Snapr</span><span>Chirpo</span><span>Worknet</span><span>Vidro</span></div>

</body>
</html>
```